Human Resource Consulting practice needs a business card design

We need a business card design (double sided colour) for our Human Resource (HR) consulting practice in regional New South Wales, australia. Our business name is Staff Compass. We support small and medium business across the Mid North Coast of New South Wales by providing them with outsourced HR support, services and products to help them achieve compliance with workplace legislation and across all areas of the employment lifecycle from recruitment to termination and everything in between. Our corporate colours are hot pink and black. The final design should communicate professionalism, trust, people focus.
I have attached the current (old) business card for your reference.

Target Market(s)

Business owners and high level managers

Industry/Entity Type

Business

Contact Information for Business Card

Name
Title
Phone no
Mobile no
Address
PO Box
email address
website

Colors
e34197

Requirements
Must have
• Tempate for changing business card personal details including Name, position title, mobile number, email address.
• Keep current logo and colours as per attached
• Logo must be presented in 2 colours or black only not white
Nice to have
• One side logo and graphic only other side logo and personal details
Should not have
• Should not be the same as the current version (attached) but a modern interpretation.
• Does not need a busy reverse side with our list of services as per current version. I feel this is too busy.
• No photos

```html
<!DOCTYPE html>
<html lang="en">
<head>
<meta charset="utf-8">
<title>Staff Compass – Business Card</title>
<link rel="stylesheet" href="https://fonts.googleapis.com/css2?family=Lato:wght@300;400;700&display=swap">
<style>
  :root {
    --hot-pink: #e34197;
    --deep-pink: #d6127f;
    --soft-pink: #ef6fb4;
    --card-white: #f7f7f7;
    --swoosh-grey: #e6e6e6;
    --ink: #222222;
    --text-grey: #555555;
    --backdrop: #d9d4cc;
  }
  * { box-sizing: border-box; margin: 0; padding: 0; }
  html, body {
    width: 1200px;
    height: 1023px;
    overflow: hidden;
    background: var(--backdrop);
    font-family: "Lato", Arial, sans-serif;
  }
  .sheet {
    width: 1200px;
    height: 1023px;
    display: flex;
    flex-direction: column;
    align-items: center;
    justify-content: center;
    gap: 60px;
  }
  .card {
    position: relative;
    width: 720px;
    height: 411px;
    border-radius: 28px;
    overflow: hidden;
    box-shadow: 0 6px 18px rgba(0,0,0,0.18);
  }

  /* Front side */
  .card--front { background: var(--card-white); }
  .card__swoosh { position: absolute; inset: 0; width: 100%; height: 100%; }
  .front__brand {
    position: absolute;
    left: 44px;
    top: 206px;
    font-size: 38px;
    font-weight: 400;
    color: var(--hot-pink);
    letter-spacing: 0.5px;
  }
  .front__details {
    position: absolute;
    right: 40px;
    top: 34px;
    text-align: right;
    color: var(--text-grey);
    font-size: 15px;
    line-height: 1.45;
    font-weight: 400;
  }
  .details__name { color: var(--hot-pink); font-weight: 700; font-size: 18px; }
  .details__title { margin-bottom: 14px; }
  .details__group { margin-bottom: 14px; }
  .details__row { display: flex; justify-content: flex-end; align-items: center; gap: 8px; }
  .details__icon { width: 13px; height: 13px; flex: none; }

  /* Back side */
  .card--back {
    background: linear-gradient(160deg, var(--deep-pink) 0%, var(--hot-pink) 55%, var(--soft-pink) 100%);
  }
  .back__brand {
    position: absolute;
    left: 56px;
    top: 120px;
    font-size: 92px;
    font-weight: 400;
    color: var(--ink);
    line-height: 1;
    letter-spacing: -1px;
  }
  .back__pattern {
    position: absolute;
    right: 0;
    bottom: 0;
    width: 300px;
    height: 200px;
    background: radial-gradient(ellipse at 100% 100%, rgba(255,255,255,0.35) 0%, rgba(255,255,255,0.12) 55%, rgba(255,255,255,0) 75%);
  }
</style>
</head>
<body>
<main class="sheet">

  <section class="card card--front" aria-label="Business card front">
    <svg class="card__swoosh" viewBox="0 0 720 411" preserveAspectRatio="none" aria-hidden="true">
      <path d="M0 300 Q380 340 720 70 L720 411 L0 411 Z" fill="var(--hot-pink)"/>
      <path d="M0 350 Q400 380 720 160 L720 215 Q420 420 0 385 Z" fill="var(--swoosh-grey)"/>
      <path d="M0 392 Q430 430 720 250 L720 411 L0 411 Z" fill="var(--deep-pink)"/>
    </svg>

    <div class="front__brand">Staff Compass</div>

    <div class="front__details">
      <p class="details__name">Megan Harlow</p>
      <p class="details__title">Principal Consultant</p>
      <div class="details__group">
        <p class="details__row">02 6500 1234
          <svg class="details__icon" viewBox="0 0 14 14" aria-hidden="true"><rect x="1" y="1" width="12" height="12" rx="2" fill="var(--hot-pink)"/><path d="M4 4h2l1 2-1 1a5 5 0 0 0 2 2l1-1 2 1v2h-1A7 7 0 0 1 4 5z" fill="#fff"/></svg>
        </p>
        <p class="details__row">0400 555 218
          <svg class="details__icon" viewBox="0 0 14 14" aria-hidden="true"><rect x="3.5" y="1" width="7" height="12" rx="1.5" fill="none" stroke="var(--hot-pink)" stroke-width="1.5"/></svg>
        </p>
      </div>
      <div class="details__group">
        <p class="details__row">megan@staffcompass.com.au
          <svg class="details__icon" viewBox="0 0 14 14" aria-hidden="true"><rect x="1" y="3" width="12" height="8" fill="var(--hot-pink)"/><path d="M1 3l6 5 6-5" fill="none" stroke="#fff" stroke-width="1.2"/></svg>
        </p>
        <p class="details__row">www.staffcompass.com.au
          <svg class="details__icon" viewBox="0 0 14 14" aria-hidden="true"><circle cx="7" cy="7" r="6" fill="var(--hot-pink)"/><path d="M1 7h12M7 1v12" stroke="#fff" stroke-width="1"/></svg>
        </p>
      </div>
      <p>P.O. Box 318, Lakeside</p>
      <p>NSW 2449</p>
    </div>
  </section>

  <section class="card card--back" aria-label="Business card back">
    <div class="back__brand">Staff Compass</div>
    <div class="back__pattern" role="img" aria-label="Scattered light pink star pattern"></div>
  </section>

</main>
</body>
</html>
```